Lotstallmart.com Webpage Design

Design Brief for lotstallmart.com (Copy of Brief also in attached Word file)

Name of Website- lotstallmart.com (existing logo and look & feel of website to be changed)

Logo - Finalised. The logo files are attached with the brief as “logo.jpeg”. The “Blue- Grey” version of the logo is for use on lighter backgrounds and the “Orange-White” version of the logo is for use on darker backgrounds. (A full Black version of the logo is also attached). Both versions may be used in different parts of the website. All attached files are in .png format.
Status - The website in functional and is undergoing user trials. However, we want to improve the look & feel of the website so at it seems
a. cotemporary,
b. Easy to Navigate
c. professional and
d. Vibrant.

Please visit ‘lotstallmart.com’ to check out the website and its functionalities – please use it only as a reference for the features & functions to be provided, however the designer should use a ‘Free Hand’ in designing the composition of various parts of the webpage without getting too influenced by the existing design

Objective of the Website ‘lotstallmart.com –
a. It is a portal focussed on listing of ‘Retail’ specific real-estate properties by developers, owners and realty brokers. The properties shall listed under the following four categories-
i. Retail Malls
ii. Shopping Complexes
iii. High-street shops
iv. Retail Warehouses
*refer lotstallmart.com for better clarity

b. The abovementioned properties shall be listed either for ‘Sale’ or ‘rent\lease’ or both

c. Users shall visit the site in case they wish to acquire a retail \ shop space either on ‘sale’ or ‘rent’. These Users would be able to specify the ‘Search Criteria’ through the tool-bars provided on the website – the ‘Search Criteria’ shall comprise of ‘Type of space category’, ‘City’, ‘Locality’, transaction type ie ‘Rent \ Sale’ and ‘Area Range’

d. The main revenue model for the website shall be listing fee ( or advertising charges ) payable by those listing their properties on the website.

Three Main Pages of Website (lotstallmart.com) that need to be designed -
a. Main Home Page (visit the web link - http://lotstallmart.com/ ) - The main home page has the “Search Toolbar” for specifying of Search Criteria by the User. It shall also have the following features & functions-
i. Main Advertising Banner
ii. Featured Projects
iii. New Launches
iv. Toolbar with buttons – ‘Advertise with Us’, ‘Listings Alert’, ‘Mart Wizards’, ‘Advertiser Login’

b. Property Listings Page (visit the web link - http://lotstallmart.com/gurgaon-in-india ) - The List of property options that match the Criteria specified by the ‘User’ get displayed on this page.

c. Property Detail Page - When the ‘User’ clicks on the “More….” Button on the ‘Property Listings Page’ (given in point b. above) the web page with the details of the property opens. (For Example – visit the web link - http://lotstallmart.com/vorne-Shopping-Complex-vorne-quadrion-gurgaon-636 )

Note:- Please refer to attached ‘Shopping’ related images the designer may use them on the website to provide a look & feel of retail if required – either separately or rotate in a single window

Target Market(s)

Retailers & Investors looking for retail space, Real Estate Brokers, Developers

Industry/Entity Type

Advertising

Number of Pages Required

3 page

Requirements
Must have
• Refer to existing site lotstallmart.com -- all the existing functionalities are a must have.
Nice to have
• The Designer may use the retail related images on the website if required for making it more vibrant. Refer attached images Shopping(1-6).jpg

```html
<!DOCTYPE html>
<html lang="en">
<head>
<meta charset="utf-8">
<title>Lotstallmart.com – Retail Space Portal</title>
<link href="https://fonts.googleapis.com/css2?family=Open+Sans:wght@400;600;700&family=Roboto:wght@400;500&display=swap" rel="stylesheet">
<style>
:root{
  --blue:#0d9bf0;
  --blue-dark:#0a86d2;
  --ink:#333;
  --muted:#777;
  --grey-btn:#6b6b6b;
  --dark:#35373b;
  --darker:#2b2d30;
  --light:#f1f1f1;
  --line:#e3e3e3;
  --orange:#f4a62a;
  --white:#fff;
}
*{box-sizing:border-box;margin:0;padding:0}
html,body{width:1200px;height:2169px;overflow:hidden}
body{font-family:"Open Sans",Arial,sans-serif;color:var(--ink);background:var(--white);position:relative}
a{color:inherit;text-decoration:none}

.city-bar{height:48px;display:flex;align-items:center;justify-content:center;font-size:11px;color:#888;border-bottom:1px solid var(--line)}
.city-bar span{padding:0 5px}

.site-header{height:107px;position:relative;border-bottom:1px solid var(--line)}
.brand{position:absolute;left:58px;top:30px;display:flex;align-items:center;gap:10px}
.brand-dot{width:38px;height:38px;border-radius:50%;background:var(--blue)}
.brand-name{font-size:30px;font-weight:700;color:var(--blue);letter-spacing:-.5px}
.main-nav{position:absolute;left:531px;top:33px;display:flex;gap:13px}
.main-nav a{height:43px;display:flex;align-items:center;justify-content:center;background:#ececec;font-size:12px;color:#777;padding:0 20px}
.main-nav a.active{background:var(--blue);color:var(--white);width:95px}
.main-nav .w-adv{width:145px}.main-nav .w-mw{width:125px}.main-nav .w-la{width:95px}.main-nav .w-lg{width:113px}

.category-bar{height:60px;background:var(--dark);display:flex;justify-content:center;gap:0}
.category{display:flex;align-items:center;gap:12px;padding:0 22px;color:var(--white);border-left:1px solid #555}
.category:first-child{border-left:none}
.category svg{flex:none}
.category b{display:block;font-size:13px;font-weight:600}
.category small{display:block;font-size:9.5px;color:#ccc}

.hero{height:537px;background:var(--light);position:relative}
.hero-slide{position:absolute;left:58px;top:19px;width:701px;height:493px;background:linear-gradient(135deg,#cfc7b4 0%,#a99c82 40%,#e98a2c 60%,#6d6a60 100%)}
.slide-arrow{position:absolute;top:224px;width:34px;height:34px;border-radius:50%;background:rgba(255,255,255,.35);display:flex;align-items:center;justify-content:center}
.slide-arrow.prev{left:18px}.slide-arrow.next{right:18px}

.search-panel{position:absolute;left:779px;top:19px;width:360px;height:493px;background:var(--blue);color:var(--white);padding:22px 30px}
.search-panel h2{text-align:center;font-size:21px;font-weight:400}
.search-panel .sub{text-align:center;font-size:11px;margin-top:4px}
.format-box{margin-top:22px;background:var(--blue-dark);padding:12px 16px;display:grid;grid-template-columns:1fr 1fr;row-gap:10px;font-size:12px}
.format-box label{display:flex;align-items:center;gap:8px}
.format-box i{width:10px;height:10px;background:var(--white);display:inline-block}
.field-label{font-size:13px;margin:16px 0 6px}
.select,.input{height:31px;background:var(--white);color:#555;font-size:11px;display:flex;align-items:center;justify-content:space-between;padding:0 12px}
.search-btn{display:block;margin:18px auto 0;width:178px;height:32px;background:var(--orange);color:#333;font-size:13px;font-weight:600;display:flex;align-items:center;justify-content:center;border:1px solid #d88e14}

.section{position:absolute;left:58px;width:1082px}
.section-head{display:flex;justify-content:space-between;align-items:center;height:30px}
.section-head h2{font-size:22px;font-weight:400;color:#444}
.pager{display:flex;gap:6px}
.pager span{width:22px;height:22px;display:flex;align-items:center;justify-content:center;background:#555}
.pager span.on{background:var(--blue)}
.cards{display:grid;grid-template-columns:repeat(5,195px);justify-content:space-between;margin-top:20px}
.card{border:1px solid var(--line);height:275px;display:flex;flex-direction:column;align-items:center;padding-top:12px}
.card-img{width:168px;height:134px}
.card h3{font-size:15px;font-weight:400;margin-top:10px}
.card h3.hl{color:var(--blue)}
.card p{font-size:11px;color:var(--muted);line-height:16px;text-align:center}
.card .btn{margin-top:auto;width:100%;height:29px;background:var(--grey-btn);color:var(--white);font-size:13px;display:flex;align-items:center;justify-content:center}
.card .btn.hl{background:var(--blue)}

.subscribe{position:absolute;left:58px;top:1168px;width:1082px;height:92px;background:var(--blue);display:flex;align-items:center;padding:0 25px;color:var(--white)}
.subscribe p{font-size:11px;line-height:15px;width:185px;margin-left:22px}
.subscribe .input{width:175px;height:29px;margin-left:14px}
.subscribe .select{width:185px;height:29px;margin-left:10px}
.subscribe .sub-btn{margin-left:40px;width:148px;height:30px;background:var(--orange);color:#333;font-weight:600;font-size:13px;display:flex;align-items:center;justify-content:center}

.site-footer{position:absolute;left:0;top:1706px;width:1200px;height:394px;background:var(--dark);color:#9a9a9a;font-size:11px;line-height:16px}
.fcol{position:absolute;top:72px}
.fcol h4{color:#e2e2e2;font-size:16px;font-weight:500;font-family:Roboto,Arial,sans-serif;display:flex;align-items:center;gap:10px;margin-bottom:28px}
.fcol h4 .dot{width:14px;height:14px;border-radius:50%;background:var(--blue)}
.fcol .gap{height:22px}
.fcol .link{color:var(--blue)}
.links{display:grid;grid-template-columns:130px 120px;row-gap:8px}
.contact-field{width:253px;height:34px;background:var(--darker);margin-top:4px;display:flex;align-items:center;padding:0 14px;color:#bbb}
.submit{margin:12px 0 0 118px;width:135px;height:33px;background:var(--blue);color:var(--white);display:flex;align-items:center;justify-content:center;font-size:13px}

.bottom-bar{position:absolute;left:0;top:2100px;width:1200px;height:69px;background:#26282b;color:#777;font-size:11px}
.bottom-bar .brand-name{position:absolute;left:58px;top:18px;font-size:24px;color:var(--white)}
.bottom-bar .copy{position:absolute;left:478px;top:27px}
.socials{position:absolute;left:940px;top:22px;display:flex;gap:12px}
.socials span{width:24px;height:24px;border-radius:50%;background:#444}
.socials span.on{background:var(--blue)}
</style>
</head>
<body>

<div class="city-bar">
  <span>Bangalore</span>|<span>Chennai</span>|<span>Greater Noida</span>|<span>Gurgaon</span>|<span>Hyderabad</span>|<span>Jaipur</span>|<span>Khanna</span>|<span>Kolkatta</span>|<span>Mumbai</span>|<span>Noida</span>|<span>Pune</span>|<span>Surat</span>
</div>

<header class="site-header">
  <div class="brand"><span class="brand-dot"></span><span class="brand-name">lotstallmart</span></div>
  <nav class="main-nav">
    <a class="active">Home</a>
    <a class="w-adv">Advertise with us</a>
    <a class="w-mw">Mart Wizards</a>
    <a class="w-la">Listing Alert</a>
    <a class="w-lg">Advertiser Login</a>
  </nav>
</header>

<div class="category-bar">
  <div class="category"><svg width="20" height="20" viewBox="0 0 20 20"><circle cx="10" cy="10" r="10" fill="#fff"/><path d="M5 10l3.5 3.5L15 7" stroke="#35373b" stroke-width="2.4" fill="none"/></svg><div><b>Retail Malls</b><small>Centrally Air-Conditioned</small></div></div>
  <div class="category"><svg width="20" height="20" viewBox="0 0 20 20"><circle cx="10" cy="10" r="10" fill="#fff"/><path d="M5 10l3.5 3.5L15 7" stroke="#35373b" stroke-width="2.4" fill="none"/></svg><div><b>Shopping Complex</b><small>Non Air-Conditioned Building</small></div></div>
  <div class="category"><svg width="20" height="20" viewBox="0 0 20 20"><circle cx="10" cy="10" r="10" fill="#fff"/><path d="M5 10l3.5 3.5L15 7" stroke="#35373b" stroke-width="2.4" fill="none"/></svg><div><b>High Street Shops</b><small>Non Air-Conditioned Building</small></div></div>
  <div class="category"><svg width="20" height="20" viewBox="0 0 20 20"><circle cx="10" cy="10" r="10" fill="#fff"/><path d="M5 10l3.5 3.5L15 7" stroke="#35373b" stroke-width="2.4" fill="none"/></svg><div><b>Retail Warehouses</b><small>Back-end Retail Storage</small></div></div>
</div>

<section class="hero">
  <div class="hero-slide" role="img" aria-label="Shopper with colourful bags inside a bright shopping mall">
    <span class="slide-arrow prev"><svg width="12" height="14"><path d="M9 2L3 7l6 5" stroke="#fff" stroke-width="2" fill="none"/></svg></span>
    <span class="slide-arrow next"><svg width="12" height="14"><path d="M3 2l6 5-6 5" stroke="#fff" stroke-width="2" fill="none"/></svg></span>
  </div>
  <form class="search-panel">
    <h2>Search your place Now</h2>
    <div class="sub">Select Retail Format: Meaning of Retail Format</div>
    <div class="format-box">
      <label><i></i>Retail Malls</label><label><i></i>Shopping Complex</label>
      <label><i></i>High Street Shop</label><label><i></i>Retail Warehouses</label>
    </div>
    <div class="field-label">Sale Or Rent Or Both:</div>
    <div class="select">Both<svg width="14" height="8"><path d="M1 1l6 6 6-6" stroke="#555" stroke-width="1.5" fill="none"/></svg></div>
    <div class="field-label">Select City:</div>
    <div class="select">--Select--<svg width="14" height="8"><path d="M1 1l6 6 6-6" stroke="#555" stroke-width="1.5" fill="none"/></svg></div>
    <div class="field-label">Select Locality/Micro-Market.</div>
    <div class="select">--Select--<svg width="14" height="8"><path d="M1 1l6 6 6-6" stroke="#555" stroke-width="1.5" fill="none"/></svg></div>
    <div class="field-label">Enter Keywords:</div>
    <div class="input">Name of the project</div>
    <span class="search-btn">SEARCH</span>
  </form>
</section>

<section class="section" style="top:792px">
  <div class="section-head"><h2>Featured Projects</h2><div class="pager"><span><svg width="8" height="10"><path d="M6 1L2 5l4 4" stroke="#fff" stroke-width="2" fill="none"/></svg></span><span class="on"><svg width="8" height="10"><path d="M2 1l4 4-4 4" stroke="#fff" stroke-width="2" fill="none"/></svg></span></div></div>
  <div class="cards">
    <article class="card"><div class="card-img" role="img" aria-label="Mall exterior with glass towers" style="background:linear-gradient(#6a7b8c,#3e4650)"></div><h3 class="hl">Surat</h3><p>Vela 81 High Street<br>Sector-81<br>Shopping Complex</p><a class="btn hl">View The Listings</a></article>
    <article class="card"><div class="card-img" role="img" aria-label="Illustrated mall atrium with shops" style="background:linear-gradient(#9ed3d0,#c4926a)"></div><h3>Surat</h3><p>Vela 81 High Street<br>Sector-81<br>Shopping Complex</p><a class="btn">View The Listings</a></article>
    <article class="card"><div class="card-img" role="img" aria-label="Bright mall interior with escalator" style="background:linear-gradient(#e6eae8,#8d9994)"></div><h3>Surat</h3><p>Vela 81 High Street<br>Sector-81<br>Shopping Complex</p><a class="btn">View The Listings</a></article>
    <article class="card"><div class="card-img" role="img" aria-label="Modern high-rise towers under blue sky" style="background:linear-gradient(#2f6fc6,#1b3566)"></div><h3>Surat</h3><p>Vela 81 High Street<br>Sector-81<br>Shopping Complex</p><a class="btn">View The Listings</a></article>
    <article class="card"><div class="card-img" role="img" aria-label="Mall building lit at night" style="background:linear-gradient(#27267a,#3b6ad0)"></div><h3>Surat</h3><p>Vela 81 High Street<br>Sector-81<br>Shopping Complex</p><a class="btn">View The Listings</a></article>
  </div>
</section>

<div class="subscribe">
  <svg width="48" height="48" viewBox="0 0 48 48"><circle cx="24" cy="24" r="24" fill="#fff"/><rect x="11" y="16" width="26" height="18" fill="none" stroke="#0d9bf0" stroke-width="2.5"/><path d="M11 16l13 11 13-11" stroke="#0d9bf0" stroke-width="2.5" fill="none"/></svg>
  <p>Suscribe for Fortnightly Email update on New Listings @ Lotstallmart.com</p>
  <div class="input">Listing Alert</div>
  <div class="select">Select Options<svg width="8" height="12"><path d="M1 4l3-3 3 3M1 8l3 3 3-3" stroke="#555" fill="none"/></svg></div>
  <div class="select">Adilabad<svg width="10" height="6"><path d="M0 0h10L5 6z" fill="#555"/></svg></div>
  <span class="sub-btn">SUBSRIBE</span>
</div>

<section class="section" style="top:1301px">
  <div class="section-head"><h2>New Launches</h2><div class="pager"><span><svg width="8" height="10"><path d="M6 1L2 5l4 4" stroke="#fff" stroke-width="2" fill="none"/></svg></span><span class="on"><svg width="8" height="10"><path d="M2 1l4 4-4 4" stroke="#fff" stroke-width="2" fill="none"/></svg></span></div></div>
  <div class="cards">
    <article class="card"><div class="card-img" role="img" aria-label="Multi-level mall interior" style="background:linear-gradient(#dfe3e4,#9aa4a8)"></div><h3 class="hl">Surat</h3><p>Vela 81 High Street<br>Sector-81<br>Shopping Complex</p><a class="btn hl">View The Listings</a></article>
    <article class="card"><div class="card-img" role="img" aria-label="Mall corridor with ceiling lights" style="background:linear-gradient(#4d5358,#c9cdd0)"></div><h3>Surat</h3><p>Vela 81 High Street<br>Sector-81<br>Shopping Complex</p><a class="btn">View The Listings</a></article>
    <article class="card"><div class="card-img" role="img" aria-label="Low retail building under blue sky" style="background:linear-gradient(#6fa3d8,#c9b89a)"></div><h3>Surat</h3><p>Vela 81 High Street<br>Sector-81<br>Shopping Complex</p><a class="btn">View The Listings</a></article>
    <article class="card"><div class="card-img" role="img" aria-label="Brick shopping centre with clouds" style="background:linear-gradient(#5f93cf,#a97b5c)"></div><h3>Surat</h3><p>Vela 81 High Street<br>Sector-81<br>Shopping Complex</p><a class="btn">View The Listings</a></article>
    <article class="card"><div class="card-img" role="img" aria-label="Waterfront skyline at dusk" style="background:linear-gradient(#3b6fb5,#d8c8b4)"></div><h3>Surat</h3><p>Vela 81 High Street<br>Sector-81<br>Shopping Complex</p><a class="btn">View The Listings</a></article>
  </div>
</section>

<footer class="site-footer">
  <div class="fcol" style="left:65px;width:230px">
    <h4>WWW.LOTSTALLMART.COM</h4>
    <p>Lotstallmart.com - About Us<br>Lotstallmart.com is a Specialised Web based platform for Retail Space, featuring properties</p>
    <div class="gap"></div>
    <p>Stall Central<br>Unit 512, 5th Floor,<br>Lorem Ipsum is simply,<br>Sector-x, Gurgaon - 122002</p>
    <div class="gap"></div>
    <p>Phone : 000-000-0000<br>Fax : 000 - 000 - 0000</p>
  </div>
  <div class="fcol" style="left:325px;width:220px">
    <h4><span class="dot"></span>CHIRPER</h4>
    <p>In hac habitasse platea dictumst. Nam pulvinar, odio sed rhoncus suscipit<br><span class="link">http://lsm.co/qR4d8KpLm 2 days ago</span></p>
    <div class="gap"></div>
    <p>RT <span class="link">@MiraLane</span>: Proin metus odio, aliquam eget molestie nec, gravida ut sapien. Phasellus quis est<br><span class="link">http://lsm.co/Tn2WxB7cE 8 days ago</span></p>
  </div>
  <div class="fcol" style="left:590px;width:260px">
    <h4><span class="dot"></span>ABOUT STALL CENTRAL</h4>
    <div class="links">
      <span>About Us</span><span>Retail Malls</span>
      <span>Privacy Policy</span><span>Shopping Complex</span>
      <span>Terms of Use</span><span>High Street Shops</span>
      <span>Contact Us</span><span>Retail Warehouses</span>
      <span>Site Map</span><span></span>
    </div>
  </div>
  <div class="fcol" style="left:885px;width:260px">
    <h4><span class="dot"></span>CONTACT</h4>
    <p>Post your Retail Space requirement with us and our experts shall get back with suitable options and even help you in your transaction. This is a Free Service!</p>
    <div style="height:14px"></div>
    <div class="contact-field">Enter your email adress</div>
    <div class="contact-field">Mobile</div>
    <div class="contact-field">Description</div>
    <span class="submit">SUBMIT</span>
  </div>
</footer>

<div class="bottom-bar">
  <span class="brand-name">lotstallmart</span>
  <span class="copy">© 2014 yoursite All Rights Reserved.</span>
  <div class="socials"><span></span><span class="on"></span><span></span><span></span><span></span><span></span></div>
</div>

</body>
</html>
```